Business Card Design (NEW FILES)

ATTENTION: New vector files are available. Please update your design to reflect/use the new (better resolution) logo images.

Seeking a unique and professional business card design for a commercial drone photography/videography business. The layout should feature
the logo (attached) and include the following information:
Owen Tarrick
614-502-7738
www.skylarkreelworks.example
NRD Certified Remote Pilot

Owen Tarrick

```html
<!DOCTYPE html>
<html lang="en">
<head>
<meta charset="utf-8">
<title>Skylark Reelworks – Business Card</title>
<link href="https://fonts.googleapis.com/css2?family=Open+Sans:wght@400;600;700;800&display=swap" rel="stylesheet">
<style>
  :root {
    --stage: #232323;
    --navy: #1b1b4b;
    --navy-deep: #15163e;
    --navy-light: #2b3580;
    --orange: #f0884a;
    --white: #ffffff;
  }
  * { margin: 0; padding: 0; box-sizing: border-box; }
  html, body {
    width: 1200px; height: 780px; overflow: hidden;
    background: var(--stage);
    font-family: "Open Sans", Arial, sans-serif;
  }
  .stage {
    width: 1200px; height: 780px;
    display: flex; align-items: center; justify-content: center; gap: 40px;
  }
  .card {
    position: relative;
    width: 560px; height: 320px;
    background: var(--navy);
    overflow: hidden;
  }
  /* back side */
  .back-pattern {
    position: absolute; inset: 0;
    background: linear-gradient(135deg, var(--navy-light) 0%, var(--navy) 55%, var(--navy-deep) 100%);
  }
  .back-brand {
    position: absolute; right: 56px; bottom: 64px;
    display: flex; align-items: center; gap: 8px;
    color: var(--white); font-size: 15px; font-weight: 600; letter-spacing: .5px;
  }
  .brand-dot {
    width: 12px; height: 12px; border-radius: 50%; background: var(--orange);
  }
  /* front side */
  .front-brand {
    position: absolute; left: 36px; top: 62px;
    display: flex; align-items: center; gap: 12px;
    color: var(--white); font-size: 26px; font-weight: 600; letter-spacing: .5px;
  }
  .front-brand .brand-dot { width: 20px; height: 20px; }
  .name-bar {
    position: absolute; right: 0; top: 30px;
    width: 14px; height: 48px; background: var(--orange);
  }
  .holder {
    position: absolute; right: 28px; top: 26px; text-align: right;
  }
  .holder-name {
    color: var(--orange); font-size: 26px; font-weight: 800; line-height: 1.1;
  }
  .holder-role {
    color: var(--white); font-size: 13px; font-weight: 400;
  }
  .credentials {
    position: absolute; left: 40px; top: 190px;
    color: var(--white); font-size: 13px; line-height: 1.35;
  }
  .contacts {
    position: absolute; left: 40px; bottom: 22px;
    list-style: none; color: var(--white); font-size: 13px; line-height: 1.5;
  }
  .contacts li { display: flex; align-items: center; gap: 8px; }
  .contacts svg { width: 12px; height: 12px; flex: none; }
  .drone-art {
    position: absolute; right: 20px; bottom: 30px;
    width: 240px; height: 130px; border-radius: 60px 60px 20px 60px;
    background: radial-gradient(ellipse at 65% 30%, rgba(240,136,74,.45) 0%, rgba(43,53,128,.7) 45%, rgba(27,27,75,0) 80%);
  }
</style>
</head>
<body>
<main class="stage">

  <section class="card card-back" aria-label="Card back">
    <div class="back-pattern" role="img" aria-label="Repeating embossed drone pattern"></div>
    <div class="back-brand"><span class="brand-dot"></span>Skylark Reelworks</div>
  </section>

  <section class="card card-front" aria-label="Card front">
    <div class="front-brand"><span class="brand-dot"></span>Skylark Reelworks</div>

    <span class="name-bar"></span>
    <div class="holder">
      <p class="holder-name">Owen Tarrick</p>
      <p class="holder-role">Owner</p>
    </div>

    <div class="drone-art" role="img" aria-label="Embossed drone with camera illustration"></div>

    <p class="credentials">NRD Certified Remote Pilot<br>Fully Insured</p>

    <ul class="contacts">
      <li>
        <svg viewBox="0 0 24 24" aria-hidden="true"><path fill="var(--orange)" d="M6.6 10.8a15 15 0 0 0 6.6 6.6l2.2-2.2c.3-.3.7-.4 1-.2 1.1.4 2.3.6 3.6.6.6 0 1 .4 1 1V20c0 .6-.4 1-1 1A17 17 0 0 1 3 4c0-.6.4-1 1-1h3.5c.6 0 1 .4 1 1 0 1.3.2 2.5.6 3.6.1.3 0 .7-.2 1z"/></svg>
        614-502-7738
      </li>
      <li>
        <svg viewBox="0 0 24 24" aria-hidden="true"><circle cx="12" cy="12" r="9" fill="none" stroke="var(--orange)" stroke-width="2"/><path d="M3 12h18M12 3c3 3 3 15 0 18M12 3c-3 3-3 15 0 18" fill="none" stroke="var(--orange)" stroke-width="1.6"/></svg>
        www.skylarkreelworks.example
      </li>
      <li>
        <svg viewBox="0 0 24 24" aria-hidden="true"><rect x="3" y="6" width="18" height="13" rx="1" fill="none" stroke="var(--orange)" stroke-width="2"/><path d="M3 7l9 7 9-7" fill="none" stroke="var(--orange)" stroke-width="2"/></svg>
        info@skylarkreelworks.example
      </li>
    </ul>
  </section>

</main>
</body>
</html>
```